Design concept Visual UI of future mobile app - healthcare

Hi,
I'm looking for a top designer, innovative with strong experience in user interface

The app will be connected to a future health website related to depression and addiction by helping the user to track the moods, tired, anxiety using this mobile app.

I attached the deck of the overall project but I can send you a specific presentation for the app only

thanks

Target Market(s)

Switzerland, UK, Germany and France

Industry/Entity Type

Mental Health

Logo Text

Health, hope

Font styles to use
Sans Serif

Colors
cee9f5
33a6d7
0692cd
0255a3
3276b5
85abd2

Requirements
Must have
• keep it simple, easy to navigate
• The user should be able to track the moods on a daily basis,
• sleep time, and rate how the feel on the day
• To be able to get information from the sync deck of vexlo
Nice to have
• to be able share this app with a friend

```html
<!DOCTYPE html>
<html lang="en">
<head>
<meta charset="utf-8">
<title>Tracking Graphs – Mood App Screens</title>
<link href="https://fonts.googleapis.com/css2?family=Roboto:wght@300;400;500&display=swap" rel="stylesheet">
<style>
  :root {
    --page: #f2f2f2;
    --sky-top: #3592d3;
    --sky-mid: #44a2dc;
    --sky-low: #62b5e4;
    --bar: rgba(255,255,255,0.12);
    --text: #ffffff;
    --label: #e6f3fb;
  }
  * { box-sizing: border-box; margin: 0; padding: 0; }
  html, body { width: 1200px; height: 800px; overflow: hidden; }
  body {
    background: var(--page);
    font-family: "Roboto", "Helvetica Neue", Arial, sans-serif;
    position: relative;
    color: var(--text);
  }
  .screen {
    position: absolute;
    top: 227px;
    width: 190px;
    height: 335px;
    overflow: hidden;
  }
  .screen--week { left: 233px; }
  .screen--month { left: 510px; }
  .screen--year { left: 786px; }
  .sky {
    position: absolute; inset: 0;
    background: linear-gradient(180deg, var(--sky-top) 0%, var(--sky-mid) 55%, var(--sky-low) 100%);
  }
  .status-bar {
    position: absolute; top: 0; left: 0; right: 0; height: 14px;
    display: flex; align-items: center; justify-content: space-between;
    padding: 0 5px; font-size: 5.5px; font-weight: 400;
  }
  .status-bar .carrier, .status-bar .battery { display: flex; align-items: center; gap: 3px; }
  .battery-icon { width: 12px; height: 5px; background: #fff; border-radius: 1px; display: inline-block; }
  .nav-bar {
    position: absolute; top: 20px; left: 0; right: 0; height: 24px;
    background: var(--bar);
    display: flex; align-items: center; padding: 0 14px 0 20px;
    font-size: 12px; font-weight: 300;
  }
  .nav-bar .menu { width: 10px; height: 8px; display: flex; flex-direction: column; justify-content: space-between; margin-right: 10px; }
  .nav-bar .menu span { height: 1.4px; background: #fff; display: block; }
  .nav-bar .next { margin-left: auto; }
  .title {
    position: absolute; left: 0; right: 0; top: 46px;
    text-align: center; font-size: 11px; font-weight: 400; letter-spacing: 0.2px;
  }
  .period {
    position: absolute; left: 0; right: 0;
    text-align: center; font-size: 10px; font-weight: 300;
  }
  .year-label {
    position: absolute; left: 0; right: 0; top: 79px;
    text-align: center; font-size: 11px; font-weight: 500;
  }
  .chart { position: absolute; }
  .axis {
    position: absolute; display: flex; justify-content: space-between;
    font-size: 4.5px; color: var(--label);
  }
  .y-axis {
    position: absolute; font-size: 4.5px; color: var(--label);
    display: flex; flex-direction: column; gap: 8px;
  }
</style>
</head>
<body>

  <section class="screen screen--week">
    <div class="sky" role="img" aria-label="Sky background photo"></div>
    <div class="status-bar">
      <span class="carrier">●●●○○ NOVA</span><span>4:21 PM</span>
      <span class="battery">100% <i class="battery-icon"></i></span>
    </div>
    <nav class="nav-bar"><div class="menu"><span></span><span></span><span></span></div><span>&lt;</span><span class="next">&gt;</span></nav>
    <h1 class="title">TRACKING GRAPHS</h1>
    <p class="period" style="top:67px">Week</p>
    <svg class="chart" style="left:26px;top:86px" width="143" height="177" viewBox="0 0 143 177">
      <defs><clipPath id="weekClip"><rect width="143" height="177" rx="4"/></clipPath></defs>
      <g clip-path="url(#weekClip)">
        <rect y="0" width="143" height="18" fill="#e8401a"/>
        <rect y="18" width="143" height="18" fill="#ef5f12"/>
        <rect y="36" width="143" height="18" fill="#f27d10"/>
        <rect y="54" width="143" height="17" fill="#e6b044"/>
        <rect y="71" width="143" height="18" fill="#a3a11c"/>
        <rect y="89" width="143" height="18" fill="#96991c"/>
        <rect y="107" width="143" height="18" fill="#879027"/>
        <rect y="125" width="143" height="18" fill="#7c853c"/>
        <rect y="143" width="143" height="17" fill="#73764f"/>
        <rect y="160" width="143" height="17" fill="#6d6c62"/>
      </g>
      <g stroke="#fff" stroke-opacity="0.7" stroke-width="0.6">
        <line x1="17.8" y1="0" x2="17.8" y2="177"/><line x1="35.7" y1="0" x2="35.7" y2="177"/>
        <line x1="53.6" y1="0" x2="53.6" y2="177"/><line x1="71.5" y1="0" x2="71.5" y2="177"/>
        <line x1="89.4" y1="0" x2="89.4" y2="177"/><line x1="107.2" y1="0" x2="107.2" y2="177"/>
        <line x1="125.1" y1="0" x2="125.1" y2="177"/>
      </g>
      <g fill="#fff">
        <circle cx="8" cy="62" r="1.6"/><circle cx="26" cy="43" r="1.6"/><circle cx="43" cy="43" r="1.6"/>
        <circle cx="62" cy="26" r="1.6"/><circle cx="80" cy="61" r="1.6"/><circle cx="98" cy="79" r="1.6"/>
        <circle cx="115" cy="115" r="1.6"/><circle cx="133" cy="62" r="1.6"/>
      </g>
    </svg>
    <div class="axis" style="left:28px;top:265px;width:140px">
      <span>Mon</span><span>Tue</span><span>Wed</span><span>Thu</span><span>Fri</span><span>Sat</span><span>Sun</span><span>Mon</span>
    </div>
  </section>

  <section class="screen screen--month">
    <div class="sky" role="img" aria-label="Sky background photo"></div>
    <div class="status-bar">
      <span class="carrier">●●●○○ NOVA</span><span>4:21 PM</span>
      <span class="battery">100% <i class="battery-icon"></i></span>
    </div>
    <nav class="nav-bar"><div class="menu"><span></span><span></span><span></span></div><span>&lt;</span><span class="next">&gt;</span></nav>
    <h1 class="title">TRACKING GRAPHS</h1>
    <p class="period" style="top:66px">Month</p>
    <p class="year-label">2015</p>
    <svg class="chart" style="left:35px;top:101px" width="125" height="145" viewBox="0 0 125 145">
      <defs>
        <linearGradient id="moodMonth" x1="0" y1="0" x2="0" y2="1">
          <stop offset="0" stop-color="#ec4a22"/><stop offset="0.3" stop-color="#f07e18"/>
          <stop offset="0.42" stop-color="#e0a830"/><stop offset="0.55" stop-color="#9a9e22"/>
          <stop offset="0.8" stop-color="#7c8740"/><stop offset="1" stop-color="#6d6c62"/>
        </linearGradient>
      </defs>
      <rect width="125" height="145" rx="5" fill="url(#moodMonth)"/>
      <g stroke="#fff" stroke-opacity="0.25" stroke-width="0.5">
        <line x1="18" y1="0" x2="18" y2="145"/><line x1="36" y1="0" x2="36" y2="145"/>
        <line x1="54" y1="0" x2="54" y2="145"/><line x1="72" y1="0" x2="72" y2="145"/>
        <line x1="90" y1="0" x2="90" y2="145"/><line x1="108" y1="0" x2="108" y2="145"/>
      </g>
      <path d="M0 72 C8 70 14 66 22 72 C28 78 32 60 38 64 C44 68 46 74 50 58 C54 44 58 60 62 74 C66 86 70 90 76 70 C80 56 86 62 90 80 C94 96 100 108 106 100 C112 92 116 84 125 86"
            fill="none" stroke="#fff" stroke-width="0.9"/>
    </svg>
    <div class="axis" style="left:40px;top:251px;width:115px">
      <span>Jan</span><span>Feb</span><span>Mar</span><span>Apr</span><span>May</span><span>Jun</span><span>Jul</span>
    </div>
  </section>

  <section class="screen screen--year">
    <div class="sky" role="img" aria-label="Sky background photo"></div>
    <div class="status-bar">
      <span class="carrier">●●●○○ NOVA</span><span>4:21 PM</span>
      <span class="battery">100% <i class="battery-icon"></i></span>
    </div>
    <nav class="nav-bar"><div class="menu"><span></span><span></span><span></span></div><span>&lt;</span><span class="next">&gt;</span></nav>
    <h1 class="title">TRACKING GRAPHS</h1>
    <p class="period" style="top:64px">Year</p>
    <svg class="chart" style="left:35px;top:80px" width="125" height="152" viewBox="0 0 125 152">
      <defs>
        <linearGradient id="moodYear" x1="0" y1="0" x2="0" y2="1">
          <stop offset="0" stop-color="#ec4322"/><stop offset="0.25" stop-color="#f07c18"/>
          <stop offset="0.4" stop-color="#e2a832"/><stop offset="0.55" stop-color="#9c9e22"/>
          <stop offset="0.8" stop-color="#7c8740"/><stop offset="1" stop-color="#6d6c62"/>
        </linearGradient>
      </defs>
      <rect width="125" height="152" rx="5" fill="url(#moodYear)"/>
      <g stroke="#fff" stroke-opacity="0.25" stroke-width="0.5">
        <line x1="18" y1="0" x2="18" y2="152"/><line x1="36" y1="0" x2="36" y2="152"/>
        <line x1="54" y1="0" x2="54" y2="152"/><line x1="72" y1="0" x2="72" y2="152"/>
        <line x1="90" y1="0" x2="90" y2="152"/><line x1="108" y1="0" x2="108" y2="152"/>
      </g>
      <g fill="none" stroke="#fff" stroke-width="0.9">
        <path d="M0 62 C10 56 16 70 24 58 C30 48 36 52 42 60 C48 68 52 44 58 42 C64 40 66 58 72 70 C78 80 82 58 88 54 C96 48 100 70 106 74 C112 78 118 60 125 62"/>
        <path d="M0 72 C8 66 14 60 22 64 C30 68 34 80 40 72 C46 64 50 56 56 66 C62 76 66 54 74 58 C80 62 84 74 90 62 C96 52 100 64 106 80 C112 92 118 82 125 86"/>
        <path d="M0 78 C10 74 16 82 24 72 C30 64 36 80 44 84 C50 88 54 70 60 72 C66 74 70 88 76 86 C82 84 86 98 92 108 C98 116 104 90 110 96 C116 102 120 108 125 104"/>
      </g>
      <g fill="#fff">
        <circle cx="16" cy="52" r="0.9"/><circle cx="26" cy="48" r="0.9"/><circle cx="34" cy="56" r="0.9"/>
        <circle cx="40" cy="46" r="0.9"/><circle cx="48" cy="62" r="0.9"/><circle cx="54" cy="50" r="0.9"/>
        <circle cx="62" cy="56" r="0.9"/><circle cx="68" cy="64" r="0.9"/><circle cx="76" cy="68" r="0.9"/>
        <circle cx="82" cy="74" r="0.9"/><circle cx="88" cy="80" r="0.9"/><circle cx="94" cy="70" r="0.9"/>
        <circle cx="100" cy="86" r="0.9"/><circle cx="106" cy="92" r="0.9"/><circle cx="112" cy="98" r="0.9"/>
        <circle cx="118" cy="90" r="0.9"/><circle cx="30" cy="78" r="0.9"/><circle cx="58" cy="84" r="0.9"/>
      </g>
    </svg>
    <div class="y-axis" style="left:20px;top:138px"><span>2016</span><span>2015</span><span>2014</span></div>
    <div class="axis" style="left:40px;top:234px;width:115px">
      <span>Jan</span><span>Feb</span><span>Mar</span><span>Apr</span><span>May</span><span>Jun</span><span>Jul</span>
    </div>
  </section>

</body>
</html>
```